VELTAR WEBSITE

need to create a new website for VELTAR ltd
the company deals with all aspects of safety products & safety wear
we need a simple website to show
ideas can be taken from following website whose products we shall distribute in kenya
www.kwr.co.uk
www.dorvik.eu
www.brimtoolsupplyco.com
www.gardvalewerks.co.za

we need following tabs
1) home - basic company information
2) products - broken down to following categories ie gloves, head protection, ear protection, mouth protection, foot protection
3) contacts

the company profile is a reputable company dealing with all aspects of safety, HSE (health and safety equipment), and PPE (personal protective equipment)

the website should have the dorvik logo for which we are an authorized distributor.
the dorvi industrial range writeup can be picked from their website
Updates

Dear Designers, i shall be able to choose a final design in 2 weeks, sorry i have not been able to finalise this due to a personal reason

Target Market(s)

the buyers are all types of industry who care for their employees safety

Industry/Entity Type

Industrial

Requirements
Must have
• clean look, fresh look, user freindly
Nice to have
• clear images, quick links etc

```html
<!DOCTYPE html>
<html lang="en">
<head>
<meta charset="utf-8">
<title>Veltar – Safety Products</title>
<link href="https://fonts.googleapis.com/css2?family=Lato:wght@400;700;900&display=swap" rel="stylesheet">
<style>
:root{
  --yellow:#ffc400;
  --dark:#2f2f2f;
  --darker:#262626;
  --ink:#333333;
  --cream:#fdf8e6;
  --line:#e3e3e3;
  --muted:#a9a9a9;
  --blue:#2a3fd6;
}
*{margin:0;padding:0;box-sizing:border-box}
html,body{width:1088px;height:1200px;overflow:hidden}
body{position:relative;background:#fff;font-family:'Lato',sans-serif;color:var(--ink)}
.backdrop{position:absolute;left:0;top:0;width:1088px;height:910px;background:var(--dark)}
.search{position:absolute;left:907px;top:0;width:20px;height:19px;background:#e6e6e6}
.header{position:absolute;left:154px;top:22px;width:773px;height:76px;background:var(--yellow)}
.brand{position:absolute;left:44px;top:0;width:151px;height:76px;background:var(--cream);display:flex;align-items:center;justify-content:center;gap:7px}
.brand-mark{width:14px;height:14px;background:var(--ink)}
.brand-name{font-weight:900;font-size:22px;letter-spacing:1px;color:var(--ink)}
.nav a{position:absolute;top:31px;font-size:14px;color:var(--ink);text-decoration:none}
.nav-active{position:absolute;left:697px;top:20px;width:90px;height:3px;background:#fff}
.hero{position:absolute;left:154px;top:111px;width:773px;height:282px;background:#fff}
.hero-tag{position:absolute;left:44px;top:13px;width:151px;height:19px;background:var(--yellow);border-bottom:5px solid var(--ink);font-size:7px;font-weight:900;line-height:7px;padding:2px 0 0 6px;color:var(--ink)}
.hero-title{position:absolute;left:43px;top:84px;font-weight:900;font-size:38px;line-height:37px;color:var(--ink)}
.hero-title span{color:var(--yellow)}
.hero-visual{position:absolute;left:323px;top:30px;width:450px;height:252px;background:radial-gradient(ellipse at 30% 45%,var(--blue) 0,#4a5ae0 22%,#dfe2ea 45%,#f2f2f4 70%,#fff 100%)}
.dots{position:absolute;left:695px;top:12px;display:flex;gap:6px}
.dots i{width:8px;height:8px;border-radius:50%;background:var(--yellow);opacity:.6}
.dots i:first-child{opacity:1}
.grid{position:absolute;left:154px;top:393px;width:773px;height:517px;background:#fff;border-top:1px solid var(--line)}
.rule-v{position:absolute;top:0;width:1px;height:517px;background:var(--line)}
.rule-h{position:absolute;left:0;top:258px;width:773px;height:1px;background:var(--line)}
.card{position:absolute;width:200px;height:178px;border:1px solid #d6d6d6;background:#fff}
.card-title{height:38px;margin:-1px -1px 0;background:var(--yellow);font-size:13px;font-weight:700;text-align:center;line-height:39px;color:var(--ink)}
.card-photo{position:absolute;left:50px;top:46px;width:98px;height:118px;border-radius:8px}
.card-btn{position:absolute;left:60px;bottom:-11px;width:78px;height:18px;background:var(--ink);color:#fff;font-size:11px;text-align:center;line-height:18px}
.footer{position:absolute;left:154px;top:910px;width:773px;height:245px;background:var(--darker)}
.col{position:absolute;top:0;width:200px}
.col h3{position:absolute;top:33px;font-size:16px;font-weight:700;color:var(--muted);white-space:nowrap}
.col hr{position:absolute;left:0;width:200px;border:0;border-top:1px solid #3d3d3d}
.col ul{position:absolute;top:84px;list-style:none;font-size:13px;line-height:19px;color:var(--muted);letter-spacing:.5px;white-space:nowrap}
.btn{position:absolute;top:195px;height:18px;padding:0 8px;background:var(--yellow);color:var(--ink);font-size:11px;line-height:18px;white-space:nowrap}
.social{position:absolute;top:107px;left:0;display:flex;gap:36px;padding-left:11px}
.social span{width:32px;height:32px;border-radius:50%;background:#3e3e3e;display:flex;align-items:center;justify-content:center}
.partner{position:absolute;top:188px;text-align:center;color:#555}
.partner b{display:block;font-size:18px;font-weight:400;line-height:20px}
.partner small{display:block;font-size:7px;letter-spacing:1px}
.shade{position:absolute;left:154px;top:1155px;width:773px;height:45px;background:linear-gradient(#d8d8d8,#fff)}
.copy{position:absolute;left:0;top:1171px;width:1080px;text-align:center;font-size:10px;color:#555}
</style>
</head>
<body>
<div class="backdrop"></div>
<div class="search"><svg width="20" height="19" viewBox="0 0 20 19"><circle cx="9" cy="8.5" r="4" fill="none" stroke="#333" stroke-width="2"/><line x1="12" y1="11.5" x2="15.5" y2="15" stroke="#333" stroke-width="2.2"/></svg></div>
<div class="nav-active"></div>
<header class="header">
  <div class="brand"><span class="brand-mark"></span><span class="brand-name">VELTAR</span></div>
  <nav class="nav">
    <a style="left:469px">HOME</a>
    <a style="left:553px">PRODUCTS</a>
    <a style="left:665px">CONTACT</a>
  </nav>
</header>

<section class="hero">
  <div class="hero-tag">SPECIALIZED PROTECTIVE<br>&amp; INDUSTRIAL PRODUCTS</div>
  <h1 class="hero-title">GOOD<br>PRODUCTS<br><span>GREAT PRICES</span></h1>
  <div class="hero-visual" role="img" aria-label="Blue hard hat on architectural plans with hands measuring"></div>
  <div class="dots"><i></i><i></i><i></i></div>
</section>

<section class="grid">
  <div class="rule-v" style="left:266px"></div>
  <div class="rule-v" style="left:510px"></div>
  <div class="rule-h"></div>

  <div class="card" style="left:44px;top:36px"><div class="card-title">GLOVES</div><div class="card-photo" role="img" aria-label="Orange and black work glove" style="background:radial-gradient(circle,#f2a23a,#3a3a3a 70%,#fff 72%)"></div><div class="card-btn">VIEW</div></div>
  <div class="card" style="left:288px;top:36px"><div class="card-title">HEAD PROTECTION</div><div class="card-photo" role="img" aria-label="Welding helmet" style="background:radial-gradient(circle,#6a6f88,#1f2333 65%,#fff 70%)"></div><div class="card-btn">VIEW</div></div>
  <div class="card" style="left:532px;top:36px"><div class="card-title">EAR PROTECTION</div><div class="card-photo" role="img" aria-label="Yellow helmet-mounted ear muffs" style="background:radial-gradient(circle,#f2cf1a,#2b2b2b 62%,#fff 68%)"></div><div class="card-btn">VIEW</div></div>

  <div class="card" style="left:44px;top:294px"><div class="card-title">MOUTH PROTECTION</div><div class="card-photo" role="img" aria-label="Respirator mask with goggles" style="background:radial-gradient(circle,#e2d64a,#5c6470 60%,#fff 68%)"></div><div class="card-btn">VIEW</div></div>
  <div class="card" style="left:288px;top:294px"><div class="card-title">FOOT PROTECTION</div><div class="card-photo" role="img" aria-label="Black safety boot" style="background:radial-gradient(circle,#4a4a4a,#1c1c1c 55%,#fff 65%)"></div><div class="card-btn">VIEW</div></div>
  <div class="card" style="left:532px;top:294px"><div class="card-title">EYE PROTECTION</div><div class="card-photo" role="img" aria-label="Yellow face shield visor" style="background:radial-gradient(circle at 50% 30%,#f5d21c,#dfe6ee 50%,#fff 70%)"></div><div class="card-btn">VIEW</div></div>
</section>

<footer class="footer">
  <div class="col" style="left:43px">
    <h3>CUSTOMER SERVICES</h3>
    <hr style="top:76px"><hr style="top:167px">
    <ul><li>Our Distribution</li><li>Useful Links</li><li>Advanced Search</li><li>Knowledge Base</li></ul>
    <span class="btn">READ MORE</span>
  </div>
  <div class="col" style="left:287px">
    <h3>CONTACT</h3>
    <hr style="top:76px"><hr style="top:167px">
    <ul><li>48 Kestrel Road</li><li>Nairobi, WS 710450</li><li>E -mail: info@veltar.com</li><li>Telephone: +1 800 555 0142</li></ul>
    <span class="btn">CONTACT US</span>
  </div>
  <div class="col" style="left:532px">
    <h3>SHARE</h3>
    <hr style="top:76px"><hr style="top:167px">
    <div class="social">
      <span aria-label="Social network"></span>
      <span aria-label="Social network"></span>
      <span aria-label="Email"><svg width="16" height="12" viewBox="0 0 16 12"><rect width="16" height="12" rx="1.5" fill="#262626"/><path d="M1 1.5 8 7l7-5.5" fill="none" stroke="#3e3e3e" stroke-width="1.6"/></svg></span>
    </div>
    <div class="partner" style="left:-4px;width:120px"><b>Dorvik</b><small>AUTHORIZED DISTRIBUTOR</small></div>
    <div class="partner" style="left:138px;width:80px;top:196px"><b style="font-size:13px;font-weight:700;letter-spacing:1px">VELTAR</b></div>
  </div>
</footer>
<div class="shade"></div>
<div class="copy">© 2013 - Veltar</div>
</body>
</html>
```